Website offering services oriented to the metaverse and blockchain

We need an ecommerce website theme/template for a new company named Vimbral (a play on words for KORVAND the inventor of Quorvex). Vimbral will provide metaverse services such as:
• Vimbral Coin
• Vimbral wallet
• Vimbral Exchange
• Vimbral NFT
• Vimbral Tech
• Vimbral Pay
• Vimbral CaaS (community as a service)
• Vimbral CRM
• Vimbral Experience
• Vimbral Blockchain
• Vimbral Commerce
• Vimbral Space (as in outer space)
• Vimbral Art (sub of NFT)
• Vimbral Store

You can find our actual logo at the following link, in order to show us templates aligned with our brand:
https://files.brindlevault.net/share/folders/8kLmTzqWpXcVbNdRyHsEfGaUoJi2QtYxP?mode=view

Looking forward to heard back from you,

Designs look the same

We need a WordPress ecommerce website theme/template for a new company named Vimbral (a play on words for KORVAND the inventor of Quorvex). Vimbral will provide metaverse services such as: • Vimbral Coin • Vimbral wallet • Vimbral Exchange • Vimbral NFT • Vimbral Tech • Vimbral Pay • Vimbral CaaS (community as a service) • Vimbral CRM • Vimbral Experience • Vimbral Blockchain • Vimbral Commerce • Vimbral Space (as in outer space) • Vimbral Art (sub of NFT) • Vimbral Store You can find our actual logo at the following link, in order to show us templates aligned with our brand: https://files.brindlevault.net/share/folders/8kLmTzqWpXcVbNdRyHsEfGaUoJi2QtYxP?mode=view Looking forward to heard back from you,

Target Market(s)

Blockchain & Cryptocurrency Businesses

Industry/Entity Type

B2C, B2B Services.

Other font styles liked:
• Monserrat, Helvetica, Object Sans

Requirements
Nice to have
• Light background picture,
Should not have
• Arch designs

```html
<!DOCTYPE html>
<html lang="en">
<head>
<meta charset="utf-8">
<title>Vimbral – Metaverse &amp; Blockchain Services</title>
<link href="https://fonts.googleapis.com/css2?family=Montserrat:wght@400;500;600;700;800&display=swap" rel="stylesheet">
<style>
:root{
  --canvas:#f1f1f3;
  --orange:#f2431c;
  --white:#ffffff;
}
.theme-dark{
  --header-bg:#221d5f;
  --nav-text:#ffffff;
  --about-bg:linear-gradient(135deg,#2b2476,#201b62);
  --services-bg:#1f1b5c;
  --blog-bg:#1c1956;
  --card-bg:#221e62;
  --news-bg:#1f1b5c;
  --footer-bg:#1e1a58;
  --heading:#ffffff;
  --body:#d9d7f0;
  --ghost:rgba(255,255,255,.06);
  --ring:#7b3cd6;
  --btn-line:#ffffff;
  --btn-text:#ffffff;
  --input-bg:#ffffff;
  --send-bg:var(--orange);
  --send-icon:#ffffff;
  --rule:rgba(255,255,255,.2);
}
.theme-light{
  --header-bg:#ffffff;
  --nav-text:#1b1b2b;
  --about-bg:linear-gradient(135deg,#f1f3fc,#e3e8fa);
  --services-bg:#ffffff;
  --blog-bg:#f4f4f6;
  --card-bg:#ffffff;
  --news-bg:#ef3a0e;
  --footer-bg:#1d1c2a;
  --heading:#1b1b2b;
  --body:#55566a;
  --ghost:rgba(0,0,0,.05);
  --ring:#cfcfd6;
  --btn-line:var(--orange);
  --btn-text:var(--orange);
  --input-bg:transparent;
  --send-bg:#ffffff;
  --send-icon:#1b1b2b;
  --rule:rgba(255,255,255,.2);
}
*{box-sizing:border-box;margin:0;padding:0}
html,body{width:840px;height:1200px;overflow:hidden}
body{background:var(--canvas);position:relative;font-family:'Montserrat',Helvetica,sans-serif}
.page{position:absolute;top:65px;width:643px;height:2048px;transform:scale(.5227);transform-origin:0 0;overflow:hidden;box-shadow:0 2px 12px rgba(0,0,0,.08)}
.page--left{left:50px}
.page--right{left:454px}
section,header,footer{position:relative;width:643px;overflow:hidden}

.wordmark{position:absolute;display:flex;align-items:center;gap:6px;color:var(--orange);font-weight:700;letter-spacing:1px}
.wordmark .dot{width:10px;height:10px;border-radius:50%;background:var(--orange)}

.site-header{height:69px;background:var(--header-bg)}
.site-header .wordmark{left:59px;top:38px;font-size:21px}
.contact-bar{position:absolute;right:60px;top:15px;font-size:9.5px;font-weight:600;color:var(--nav-text);display:flex;align-items:center;gap:5px}
.contact-bar .ico{color:var(--orange)}
.cart{width:19px;height:19px;border-radius:50%;background:var(--orange);display:inline-block;margin-left:6px}
.main-nav{position:absolute;right:60px;top:45px;display:flex;gap:12px;font-size:8.5px;font-weight:600;color:var(--nav-text)}
.main-nav .active{color:var(--orange);position:relative}
.main-nav .active::before{content:"";position:absolute;left:9px;top:-9px;width:5px;height:5px;border-radius:50%;background:var(--orange)}

.hero{height:363px}
.hero-art{position:absolute;inset:0;background:linear-gradient(120deg,#3a1f8c 0%,#6a2bc4 30%,#3f3fd6 55%,#7a36c9 75%,#ff4a5c 100%)}
.hero-shade{position:absolute;inset:0;background:linear-gradient(90deg,rgba(40,20,110,.55),rgba(40,20,110,0) 60%)}
.hero-title{position:absolute;left:60px;top:155px;font-size:36px;font-weight:800;color:#fff;letter-spacing:.5px}
.hero-text{position:absolute;left:60px;top:206px;width:250px;font-size:13.5px;line-height:20px;color:#fff}
.btn{position:absolute;display:flex;align-items:center;justify-content:center;font-size:9.5px;font-weight:600;border:1px solid var(--btn-line);color:var(--btn-text)}
.hero .btn{left:60px;top:258px;width:123px;height:33px;border-color:#fff;color:#fff}

.ghost{position:absolute;font-weight:800;color:var(--ghost);letter-spacing:1px;white-space:nowrap}
.section-title{position:absolute;left:0;right:0;text-align:center;font-size:21px;font-weight:700;color:var(--heading)}

.about{height:306px;background:var(--about-bg);overflow:visible;z-index:2}
.about-art{position:absolute;left:18px;top:85px;width:332px;height:258px;border-radius:60px;background:linear-gradient(135deg,#6a5cf0,#c23ee0 35%,#3d3fe0 65%,#1d6cf0)}
.about .ghost{left:370px;top:40px;font-size:30px}
.about-title{position:absolute;left:369px;top:66px;font-size:21px;line-height:24px;font-weight:700;color:var(--heading)}
.about-text{position:absolute;left:369px;top:120px;width:225px;font-size:8.6px;line-height:14.7px;color:var(--body)}
.about .btn{left:369px;top:226px;width:74px;height:28px}

.services{height:490px;background:var(--services-bg)}
.services .ghost{left:0;right:0;text-align:center;top:28px;font-size:28px}
.services .section-title{top:52px}
.service{position:absolute;width:120px;margin-left:-60px;text-align:center}
.service .ring{width:84px;height:84px;margin:0 auto;border-radius:50%;border:1.5px solid var(--ring);border-top-color:transparent;display:flex;align-items:center;justify-content:center;transform:rotate(0)}
.service svg{width:34px;height:34px;stroke:var(--orange);fill:none;stroke-width:1.6}
.service .label{margin-top:14px;font-size:11px;color:var(--heading)}

.blog{height:438px;background:var(--blog-bg)}
.blog .ghost{left:0;right:0;text-align:center;top:26px;font-size:28px}
.blog .section-title{top:50px}
.post{position:absolute;top:97px;width:167px;height:247px;background:var(--card-bg)}
.post-img{height:121px}
.post h3{margin:14px 0 0 14px;font-size:11.5px;font-weight:600;color:var(--heading)}
.post .meta{margin:7px 0 0 14px;font-size:8px;color:var(--body)}
.post .meta span{color:var(--orange)}
.post p{margin:10px 14px 0 14px;font-size:8.2px;line-height:13px;color:var(--body)}
.post .more{margin:8px 0 0 14px;font-size:8.5px;font-weight:600;color:var(--orange)}
.blog .btn{left:284px;top:370px;width:74px;height:27px}

.newsletter{height:117px;background:var(--news-bg)}
.newsletter .ghost{left:58px;top:20px;font-size:30px;color:rgba(255,255,255,.08)}
.newsletter h2{position:absolute;left:59px;top:46px;font-size:20px;line-height:23px;font-weight:800;color:#fff}
.signup{position:absolute;left:272px;top:43px;width:311px;height:35px;display:flex;border:1px solid #fff}
.signup .field{flex:1;background:var(--input-bg);font-size:8px;color:#8d8da0;padding-left:12px;display:flex;align-items:center}
.theme-light .signup .field{color:#fff}
.signup .send{width:36px;background:var(--send-bg);display:flex;align-items:center;justify-content:center}
.signup .send svg{width:13px;height:13px;fill:var(--send-icon)}

.site-footer{height:265px;background:var(--footer-bg)}
.site-footer .wordmark{left:59px;top:72px;font-size:30px}
.site-footer .wordmark .dot{width:13px;height:13px}
.foot-col h4{position:absolute;top:40px;font-size:10.5px;font-weight:600;color:#fff}
.foot-list{position:absolute;top:64px;list-style:none;font-size:7.6px;line-height:14.2px;color:#fff}
.foot-list li::before{content:"✔ ";color:var(--orange);font-size:6.5px}
.foot-list li.cont::before{content:"";padding-left:11px}
.foot-contact{position:absolute;left:456px;top:64px;width:135px;font-size:7.6px;line-height:14.2px;color:#fff}
.foot-contact .ico{color:var(--orange)}
.foot-rule{position:absolute;left:59px;right:60px;top:211px;height:1px;background:var(--rule)}
.copyright{position:absolute;left:60px;top:233px;font-size:7.8px;color:#fff}
.socials{position:absolute;right:60px;top:226px;display:flex;gap:4px}
.socials span{width:24px;height:24px;border-radius:50%;border:1px solid var(--orange)}
</style>
</head>
<body>

<svg width="0" height="0" style="position:absolute" aria-hidden="true">
  <defs>
    <symbol id="i-coin" viewBox="0 0 32 32"><ellipse cx="12" cy="9" rx="8" ry="3"/><path d="M4 9v4c0 1.7 3.6 3 8 3s8-1.3 8-3V9M4 13v4c0 1.7 3.6 3 8 3M12 16v0"/><ellipse cx="20" cy="19" rx="8" ry="3"/><path d="M12 19v4c0 1.7 3.6 3 8 3s8-1.3 8-3v-4M12 23v3c0 1.7 3.6 3 8 3s8-1.3 8-3v-3"/></symbol>
    <symbol id="i-wallet" viewBox="0 0 32 32"><rect x="4" y="10" width="24" height="17" rx="2"/><path d="M8 10l4-6 4 6M14 10l4-5 4 5"/><rect x="20" y="15" width="8" height="6"/><path d="M7 24h10"/></symbol>
    <symbol id="i-exchange" viewBox="0 0 32 32"><rect x="16" y="4" width="11" height="9"/><rect x="5" y="18" width="11" height="9"/><path d="M5 14V8h7M9 5l3 3-3 3M27 18v6h-7M23 27l-3-3 3-3"/></symbol>
    <symbol id="i-nft" viewBox="0 0 32 32"><path d="M16 3l11 6.5v13L16 29 5 22.5v-13z"/><path d="M16 7l8 4.7v9.6L16 26l-8-4.7v-9.6z"/><path d="M11 20v-8l4 8v-8M17 20v-8h3M17 16h2M21 12h3M22.5 12v8"/></symbol>
    <symbol id="i-tech" viewBox="0 0 32 32"><circle cx="14" cy="16" r="5"/><path d="M14 5v4M14 23v4M3 16h4M21 16h4M6 8l3 3M19 21l3 3M6 24l3-3"/><path d="M20 8h5l3-3M22 12h6M22 20h4l2 2"/><circle cx="28" cy="5" r="1.4"/><circle cx="28" cy="22" r="1.4"/></symbol>
    <symbol id="i-pay" viewBox="0 0 32 32"><rect x="3" y="8" width="26" height="17" rx="2"/><rect x="7" y="13" width="6" height="5"/><path d="M7 21h10M20 13a3 3 0 010 5M23 11a6 6 0 010 9M26 9.5a9 9 0 010 12"/></symbol>
    <symbol id="i-caas" viewBox="0 0 32 32"><circle cx="16" cy="10" r="4.5"/><circle cx="8" cy="12" r="3.5"/><circle cx="24" cy="12" r="3.5"/><path d="M8 27v-4a8 8 0 0116 0v4zM3 24v-2a5 5 0 015-5M29 24v-2a5 5 0 00-5-5"/></symbol>
    <symbol id="i-crm" viewBox="0 0 32 32"><rect x="5" y="3" width="22" height="26"/><path d="M5 8h22M9 12h6M9 24h4"/><circle cx="19" cy="18" r="4"/><path d="M19 12v2M19 22v2M13 18h2M23 18h2"/><rect x="8" y="15" width="5" height="5"/></symbol>
    <symbol id="i-exp" viewBox="0 0 40 32"><path d="M7 11l2 4 4 .6-3 3 .7 4.4L7 21l-3.7 2 .7-4.4-3-3 4-.6zM20 9l2 4 4 .6-3 3 .7 4.4L20 19l-3.7 2 .7-4.4-3-3 4-.6zM33 11l2 4 4 .6-3 3 .7 4.4L33 21l-3.7 2 .7-4.4-3-3 4-.6z"/></symbol>
    <symbol id="i-chain" viewBox="0 0 32 32"><path d="M16 3l11 6.5v13L16 29 5 22.5v-13zM16 16l11-6.5M16 16L5 9.5M16 16v13"/><circle cx="16" cy="3" r="1.5"/><circle cx="27" cy="9.5" r="1.5"/><circle cx="5" cy="9.5" r="1.5"/><circle cx="16" cy="29" r="1.5"/><circle cx="16" cy="16" r="1.5"/></symbol>
    <symbol id="i-art" viewBox="0 0 32 32"><path d="M9 4h12l5 5v19H9z"/><path d="M21 4v5h5M12 9h6M12 12h8"/><rect x="5" y="15" width="22" height="9"/></symbol>
    <symbol id="i-cart" viewBox="0 0 32 32"><path d="M2 6h4l3 15h15l3-11H11"/><circle cx="11" cy="26" r="2"/><circle cx="22" cy="26" r="2"/><circle cx="19" cy="10" r="6"/><path d="M13 10h12M19 4v12M15 6.5c2.5 2 5.5 2 8 0M15 13.5c2.5-2 5.5-2 8 0"/></symbol>
    <symbol id="i-space" viewBox="0 0 32 32"><circle cx="16" cy="16" r="8"/><path d="M10 11C4 14 1 18 2.5 20.5S12 22 19 18s11-9 10.5-11.5S25 6 20 8"/></symbol>
    <symbol id="i-store" viewBox="0 0 32 32"><path d="M5 5h22l2 7H3z"/><path d="M3 12a3.3 3.3 0 006.5 0 3.3 3.3 0 006.5 0 3.3 3.3 0 006.5 0 3.3 3.3 0 006.5 0M5 15v13h22V15M9 28v-9h6v9M18 19h6v5h-6z"/></symbol>
    <symbol id="i-send" viewBox="0 0 16 16"><path d="M15 1L1 7l5 2 2 6z"/></symbol>
  </defs>
</svg>

<!-- ============ DARK THEME ============ -->
<div class="page page--left theme-dark">
  <header class="site-header">
    <div class="wordmark"><span class="dot"></span>VIMBRAL</div>
    <div class="contact-bar"><span class="ico">✆</span>1 888 555 0142 &nbsp;| <span class="ico">✉</span>info@vimbral.com<span class="cart"></span></div>
    <nav class="main-nav"><span class="active">HOME</span><span>ABOUT</span><span>METAVERSE SERVICES</span><span>BLOG</span><span>SHOP</span><span>CONTACT</span></nav>
  </header>

  <section class="hero">
    <div class="hero-art" role="img" aria-label="Neon futuristic city with a person wearing a VR headset"></div>
    <div class="hero-shade"></div>
    <h1 class="hero-title">VIMBRAL</h1>
    <p class="hero-text">We offering services oriented to the metaverse and blockchain</p>
    <div class="btn">EXPLORE SERVICES</div>
  </section>

  <section class="about">
    <div class="about-art" role="img" aria-label="Glowing digital network imagery with a person in VR"></div>
    <div class="ghost">ABOUT US</div>
    <h2 class="about-title">WELCOME TO<br>VIMBRAL</h2>
    <p class="about-text">Nam libero tempore, cum soluta nobis est eligendi optio cum que nihil impedit quo minus id quod max ime placeat facereo ssimus, omnis voluptas assume nda est, omnis dolor repellen dus. Temporibus autm quibusdam et aut officiis debitis aut rerum necessi tatibus saepe eveniet ut et volu.</p>
    <div class="btn">READ MORE</div>
  </section>

  <section class="services">
    <div class="ghost">SERVICES</div>
    <h2 class="section-title">METAVERSE SERVICES</h2>
    <div class="service" style="left:102px;top:103px"><div class="ring"><svg><use href="#i-coin"/></svg></div><div class="label">Vimbral Coin</div></div>
    <div class="service" style="left:207px;top:103px"><div class="ring"><svg><use href="#i-wallet"/></svg></div><div class="label">Vimbral wallet</div></div>
    <div class="service" style="left:322px;top:103px"><div class="ring"><svg><use href="#i-exchange"/></svg></div><div class="label">Vimbral Exchange</div></div>
    <div class="service" style="left:436px;top:103px"><div class="ring"><svg><use href="#i-nft"/></svg></div><div class="label">Vimbral NFT</div></div>
    <div class="service" style="left:541px;top:103px"><div class="ring"><svg><use href="#i-tech"/></svg></div><div class="label">Vimbral Tech</div></div>
    <div class="service" style="left:148px;top:221px"><div class="ring"><svg><use href="#i-pay"/></svg></div><div class="label">Vimbral Pay</div></div>
    <div class="service" style="left:254px;top:221px"><div class="ring"><svg><use href="#i-caas"/></svg></div><div class="label">Vimbral CaaS</div></div>
    <div class="service" style="left:368px;top:221px"><div class="ring"><svg><use href="#i-crm"/></svg></div><div class="label">Vimbral CRM</div></div>
    <div class="service" style="left:482px;top:221px"><div class="ring"><svg viewBox="0 0 40 32"><use href="#i-exp"/></svg></div><div class="label">Vimbral Experience</div></div>
    <div class="service" style="left:102px;top:345px"><div class="ring"><svg><use href="#i-chain"/></svg></div><div class="label">Vimbral Blockchain</div></div>
    <div class="service" style="left:207px;top:345px"><div class="ring"><svg><use href="#i-art"/></svg></div><div class="label">Vimbral Art</div></div>
    <div class="service" style="left:322px;top:345px"><div class="ring"><svg><use href="#i-cart"/></svg></div><div class="label">Vimbral Commerce</div></div>
    <div class="service" style="left:436px;top:345px"><div class="ring"><svg><use href="#i-space"/></svg></div><div class="label">Vimbral Space</div></div>
    <div class="service" style="left:541px;top:345px"><div class="ring"><svg><use href="#i-store"/></svg></div><div class="label">Vimbral Store</div></div>
  </section>

  <section class="blog">
    <div class="ghost">POST</div>
    <h2 class="section-title">OUR BLOG</h2>
    <article class="post" style="left:60px"><div class="post-img" role="img" aria-label="Glowing metaverse lettering on a circuit board" style="background:linear-gradient(135deg,#4a2c1c,#c8752e,#2a1a14)"></div><h3>Finibus Bonoruet Malo</h3><div class="meta"><span>▦</span> 03/02/2022 | <span>●</span> Admin</div><p>Nam libero tempore, cum soluta nobis est eligendi optio cumque nihil impedit quo min.</p><div class="more">READ MORE</div></article>
    <article class="post" style="left:238px"><div class="post-img" role="img" aria-label="Figure floating in blue digital space" style="background:linear-gradient(160deg,#0b1a5c,#1f5ee0,#0a2a80)"></div><h3>Finibus Bonoruet Malo</h3><div class="meta"><span>▦</span> 03/02/2022 | <span>●</span> Admin</div><p>Nam libero tempore, cum soluta nobis est eligendi optio cumque nihil impedit quo min.</p><div class="more">READ MORE</div></article>
    <article class="post" style="left:416px"><div class="post-img" role="img" aria-label="Figure standing in a green and blue virtual grid" style="background:linear-gradient(170deg,#1b2a6a,#1a5a5a,#2d8a3c)"></div><h3>Finibus Bonoruet Malo</h3><div class="meta"><span>▦</span> 03/02/2022 | <span>●</span> Admin</div><p>Nam libero tempore, cum soluta nobis est eligendi optio cumque nihil impedit quo min.</p><div class="more">READ MORE</div></article>
    <div class="btn">VIEW MORE</div>
  </section>

  <section class="newsletter">
    <div class="ghost">SUBSCRIBE</div>
    <h2>NEWSLETTER<br>SUBSCRIPTION</h2>
    <div class="signup"><div class="field">EMAIL ADDRESS</div><div class="send"><svg viewBox="0 0 16 16"><use href="#i-send"/></svg></div></div>
  </section>

  <footer class="site-footer">
    <div class="wordmark"><span class="dot"></span>VIMBRAL</div>
    <div class="foot-col"><h4 style="left:241px">Metaverse Services</h4><h4 style="left:456px">Contact Information</h4></div>
    <ul class="foot-list" style="left:241px"><li>Vimbral Coin</li><li>Vimbral wallet</li><li>Vimbral Exchange</li><li>Vimbral NFT</li><li>Vimbral Tech</li><li>Vimbral Pay</li><li>Vimbral CaaS</li><li class="cont">(community as a</li><li class="cont">service)</li></ul>
    <ul class="foot-list" style="left:336px"><li>Vimbral CRM</li><li>Vimbral Experience</li><li>Vimbral Blockchain</li><li>Vimbral Commerce</li><li>Vimbral Space</li><li class="cont">(as in outer space)</li><li>Vimbral Art</li><li class="cont">(sub of NFT)</li><li>Vimbral Store</li></ul>
    <div class="foot-contact"><span class="ico">⚲</span> 3rd Floor Halvane Bldg, 4 Orrin Row Dentmoor<br><br><span class="ico">✆</span> 1 888 555 0142<br><br><span class="ico">✉</span> info@vimbral.com</div>
    <div class="foot-rule"></div>
    <div class="copyright">© 2022, Vimbral. All Rights Reserved.</div>
    <div class="socials"><span></span><span></span><span></span></div>
  </footer>
</div>

<!-- ============ LIGHT THEME ============ -->
<div class="page page--right theme-light">
  <header class="site-header">
    <div class="wordmark"><span class="dot"></span>VIMBRAL</div>
    <div class="contact-bar"><span class="ico">✆</span>1 888 555 0142 &nbsp;| <span class="ico">✉</span>info@vimbral.com</div>
    <nav class="main-nav"><span class="active">HOME</span><span>ABOUT US</span><span>METAVERSE SERVICES</span><span>BLOG</span><span>CONTACT</span></nav>
  </header>

  <section class="hero">
    <div class="hero-art" role="img" aria-label="Neon futuristic city with a person wearing a VR headset"></div>
    <div class="hero-shade"></div>
    <h1 class="hero-title">VIMBRAL</h1>
    <p class="hero-text">We offering services oriented to the metaverse and blockchain</p>
    <div class="btn">EXPLORE SERVICES</div>
  </section>

  <section class="about">
    <div class="about-art" role="img" aria-label="Glowing digital network imagery with a person in VR"></div>
    <div class="ghost">ABOUT US</div>
    <h2 class="about-title">WELCOME TO<br>VIMBRAL</h2>
    <p class="about-text">Nam libero tempore, cum soluta nobis est eligendi optio cum que nihil impedit quo minus id quod max ime placeat facereo ssimus, omnis voluptas assume nda est, omnis dolor repellen dus. Temporibus autm quibusdam et aut officiis debitis aut rerum necessi tatibus saepe eveniet ut et volu.</p>
    <div class="btn">READ MORE</div>
  </section>

  <section class="services">
    <div class="ghost">SERVICES</div>
    <h2 class="section-title">METAVERSE SERVICES</h2>
    <div class="service" style="left:102px;top:103px"><div class="ring"><svg><use href="#i-coin"/></svg></div><div class="label">Vimbral Coin</div></div>
    <div class="service" style="left:207px;top:103px"><div class="ring"><svg><use href="#i-wallet"/></svg></div><div class="label">Vimbral wallet</div></div>
    <div class="service" style="left:322px;top:103px"><div class="ring"><svg><use href="#i-exchange"/></svg></div><div class="label">Vimbral Exchange</div></div>
    <div class="service" style="left:436px;top:103px"><div class="ring"><svg><use href="#i-nft"/></svg></div><div class="label">Vimbral NFT</div></div>
    <div class="service" style="left:541px;top:103px"><div class="ring"><svg><use href="#i-tech"/></svg></div><div class="label">Vimbral Tech</div></div>
    <div class="service" style="left:148px;top:221px"><div class="ring"><svg><use href="#i-pay"/></svg></div><div class="label">Vimbral Pay</div></div>
    <div class="service" style="left:254px;top:221px"><div class="ring"><svg><use href="#i-caas"/></svg></div><div class="label">Vimbral CaaS</div></div>
    <div class="service" style="left:368px;top:221px"><div class="ring"><svg><use href="#i-crm"/></svg></div><div class="label">Vimbral CRM</div></div>
    <div class="service" style="left:482px;top:221px"><div class="ring"><svg viewBox="0 0 40 32"><use href="#i-exp"/></svg></div><div class="label">Vimbral Experience</div></div>
    <div class="service" style="left:102px;top:345px"><div class="ring"><svg><use href="#i-chain"/></svg></div><div class="label">Vimbral Blockchain</div></div>
    <div class="service" style="left:207px;top:345px"><div class="ring"><svg><use href="#i-art"/></svg></div><div class="label">Vimbral Art</div></div>
    <div class="service" style="left:322px;top:345px"><div class="ring"><svg><use href="#i-cart"/></svg></div><div class="label">Vimbral Commerce</div></div>
    <div class="service" style="left:436px;top:345px"><div class="ring"><svg><use href="#i-space"/></svg></div><div class="label">Vimbral Space</div></div>
    <div class="service" style="left:541px;top:345px"><div class="ring"><svg><use href="#i-store"/></svg></div><div class="label">Vimbral Store</div></div>
  </section>

  <section class="blog">
    <div class="ghost">POST</div>
    <h2 class="section-title">OUR BLOG</h2>
    <article class="post" style="left:60px"><div class="post-img" role="img" aria-label="Glowing metaverse lettering on a circuit board" style="background:linear-gradient(135deg,#4a2c1c,#c8752e,#2a1a14)"></div><h3>Finibus Bonoruet Malo</h3><div class="meta"><span>▦</span> 03/02/2022 | <span>●</span> Admin</div><p>Nam libero tempore, cum soluta nobis est eligendi optio cumque nihil impedit quo min.</p><div class="more">READ MORE</div></article>
    <article class="post" style="left:238px"><div class="post-img" role="img" aria-label="Figure floating in blue digital space" style="background:linear-gradient(160deg,#0b1a5c,#1f5ee0,#0a2a80)"></div><h3>Finibus Bonoruet Malo</h3><div class="meta"><span>▦</span> 03/02/2022 | <span>●</span> Admin</div><p>Nam libero tempore, cum soluta nobis est eligendi optio cumque nihil impedit quo min.</p><div class="more">READ MORE</div></article>
    <article class="post" style="left:416px"><div class="post-img" role="img" aria-label="Figure standing in a green and blue virtual grid" style="background:linear-gradient(170deg,#1b2a6a,#1a5a5a,#2d8a3c)"></div><h3>Finibus Bonoruet Malo</h3><div class="meta"><span>▦</span> 03/02/2022 | <span>●</span> Admin</div><p>Nam libero tempore, cum soluta nobis est eligendi optio cumque nihil impedit quo min.</p><div class="more">READ MORE</div></article>
    <div class="btn">VIEW MORE</div>
  </section>

  <section class="newsletter">
    <div class="ghost">SUBSCRIBE</div>
    <h2>NEWSLETTER<br>SUBSCRIPTION</h2>
    <div class="signup"><div class="field">EMAIL ADDRESS</div><div class="send"><svg viewBox="0 0 16 16"><use href="#i-send"/></svg></div></div>
  </section>

  <footer class="site-footer">
    <div class="wordmark"><span class="dot"></span>VIMBRAL</div>
    <div class="foot-col"><h4 style="left:241px">Metaverse Services</h4><h4 style="left:456px">Contact Information</h4></div>
    <ul class="foot-list" style="left:241px"><li>Vimbral Coin</li><li>Vimbral wallet</li><li>Vimbral Exchange</li><li>Vimbral NFT</li><li>Vimbral Tech</li><li>Vimbral Pay</li><li>Vimbral CaaS</li><li class="cont">(community as a</li><li class="cont">service)</li></ul>
    <ul class="foot-list" style="left:336px"><li>Vimbral CRM</li><li>Vimbral Experience</li><li>Vimbral Blockchain</li><li>Vimbral Commerce</li><li>Vimbral Space</li><li class="cont">(as in outer space)</li><li>Vimbral Art</li><li class="cont">(sub of NFT)</li><li>Vimbral Store</li></ul>
    <div class="foot-contact"><span class="ico">⚲</span> 3rd Floor Halvane Bldg, 4 Orrin Row Dentmoor<br><br><span class="ico">✆</span> 1 888 555 0142<br><br><span class="ico">✉</span> info@vimbral.com</div>
    <div class="foot-rule"></div>
    <div class="copyright">© 2022, Vimbral. All Rights Reserved.</div>
    <div class="socials"><span></span><span></span><span></span></div>
  </footer>
</div>

</body>
</html>
```